Carpet cleaning company focused on high quality needs business cards

We are a growing company that just merged with another company and need to design a new business card. We do both residential as well as commercial cleaning. We do carpet, tile & grout, upholstery, hard floors, and stain & pet odor removal. We treat our customers like family and strive to achieve outstanding results with every job.

```html
<!DOCTYPE html>
<html lang="en">
<head>
<meta charset="utf-8">
<title>Mako's Fresh Crew Cleaning – Business Card</title>
<link href="https://fonts.googleapis.com/css2?family=Open+Sans:wght@400;600;700;800&display=swap" rel="stylesheet">
<style>
  :root {
    --backdrop: #d9d9d9;
    --card: #ffffff;
    --ink: #1f1d1e;
    --text: #2b2b2b;
    --brand-red: #ef443c;
    --brand-blue: #0a7dc2;
  }
  * { box-sizing: border-box; margin: 0; padding: 0; }
  html, body { width: 1200px; height: 588px; overflow: hidden; }
  body {
    background: var(--backdrop);
    font-family: "Open Sans", Arial, sans-serif;
    position: relative;
  }
  .card {
    position: absolute;
    background: var(--card);
    border-radius: 22px;
    overflow: hidden;
  }
  .card--front { left: 87px; top: 141px; width: 486px; height: 288px; }
  .card--back  { left: 622px; top: 142px; width: 490px; height: 289px; }

  .brand { position: absolute; display: flex; align-items: center; }
  .brand__square { background: var(--brand-red); flex: none; }
  .brand__name {
    color: var(--ink);
    font-weight: 800;
    line-height: 0.98;
    letter-spacing: -0.2px;
  }
  .card--front .brand { left: 69px; top: 120px; gap: 16px; }
  .card--front .brand__square { width: 104px; height: 104px; }
  .card--front .brand__name { font-size: 31px; }

  .card--back .brand { left: 47px; top: 140px; gap: 9px; }
  .card--back .brand__square { width: 64px; height: 64px; }
  .card--back .brand__name { font-size: 19px; }

  .divider {
    position: absolute; left: 282px; top: 77px;
    width: 2px; height: 137px; background: var(--brand-blue);
  }
  .contact { position: absolute; left: 298px; top: 72px; color: var(--text); }
  .contact__name { font-size: 19px; font-weight: 700; line-height: 1.2; }
  .contact__first { color: var(--brand-blue); }
  .contact__last { color: var(--brand-red); }
  .contact__title { font-size: 13px; font-weight: 600; margin-top: 1px; }
  .contact__list { list-style: none; margin-top: 9px; }
  .contact__list li {
    display: flex; align-items: center; gap: 4px;
    font-size: 13.5px; line-height: 17.5px;
  }
  .contact__list svg { width: 11px; height: 11px; flex: none; fill: var(--brand-blue); }
  .contact__address { font-size: 13.5px; line-height: 17px; margin-top: 11px; font-style: normal; }

  .wave { position: absolute; left: 0; bottom: 0; width: 490px; height: 289px; }
</style>
</head>
<body>

  <section class="card card--front" aria-label="Business card front">
    <div class="brand">
      <span class="brand__square"></span>
      <p class="brand__name">Mako's<br>Fresh Crew<br>Cleaning</p>
    </div>
  </section>

  <section class="card card--back" aria-label="Business card back">
    <div class="brand">
      <span class="brand__square"></span>
      <p class="brand__name">Mako's<br>Fresh Crew<br>Cleaning</p>
    </div>

    <span class="divider"></span>

    <div class="contact">
      <h1 class="contact__name"><span class="contact__first">Dana</span> <span class="contact__last">Morell</span></h1>
      <p class="contact__title">Executive Director</p>
      <ul class="contact__list">
        <li><svg viewBox="0 0 24 24"><path d="M6.6 10.8a15.1 15.1 0 0 0 6.6 6.6l2.2-2.2c.3-.3.7-.4 1-.2 1.1.4 2.3.6 3.6.6.6 0 1 .4 1 1V20c0 .6-.4 1-1 1A17 17 0 0 1 3 4c0-.6.4-1 1-1h3.5c.6 0 1 .4 1 1 0 1.3.2 2.5.6 3.6.1.3 0 .7-.2 1z"/></svg>123 456 789</li>
        <li><svg viewBox="0 0 24 24"><path d="M2 5h20v14H2z M2 5l10 7 10-7" fill="var(--brand-blue)"/><path d="M3 6l9 6 9-6" fill="none" stroke="#fff" stroke-width="2"/></svg>info@freshcrewmail.com</li>
        <li><svg viewBox="0 0 24 24"><circle cx="12" cy="12" r="10"/><path d="M2 12h20M12 2c3 3 3 17 0 20M12 2c-3 3-3 17 0 20" fill="none" stroke="#fff" stroke-width="1.5"/></svg>www.yourwebsite.com</li>
      </ul>
      <address class="contact__address">2716 Harbor Way<br>Lake Crest,</address>
    </div>

    <svg class="wave" viewBox="0 0 490 289" aria-hidden="true">
      <path d="M0 245 C 110 272, 240 281, 490 279 L490 289 L0 289 Z" fill="var(--brand-red)"/>
      <path d="M80 261 C 210 276, 350 276, 490 254 L490 270 C 350 283, 210 282, 80 261 Z" fill="var(--brand-blue)"/>
      <path d="M80 261 C 210 280, 350 281, 490 272" fill="none" stroke="#ffffff" stroke-width="1.5"/>
    </svg>
  </section>

</body>
</html>
```